Simple proffessional BC

I have a logo which I will attach below.
I would like the logo on the front of the card with these details in point form below:
Pre and Post Natal Yoga: Pregnancy Workshops: Hypnobirthing Courses
On the back of the card my details:
Marla Pennick
Facebook page- stretchbelliesbayridgefield
Mobile- 0491 352 718

I like the idea of the card being simple, possibly just the above on a plain coloured (eggshell?) card, a card that is textured.
I am open to suggestion if it appeals!
Thank you and good luck!

Target Market(s)

Pregnant women, 20's-40's

Requirements
Must have
• Simple, compliment logo.
Make logo the feature.
Should not have

• .

```html
<!DOCTYPE html>
<html lang="en">
<head>
<meta charset="utf-8">
<title>Stretch Bellies – Business Card</title>
<link href="https://fonts.googleapis.com/css2?family=Open+Sans:wght@400;600;700&display=swap" rel="stylesheet">
<style>
  :root {
    --page-bg: #d9d9d9;
    --card-white: #ffffff;
    --brand-red: #8a2c2d;
    --brand-orange: #f0a03a;
    --ink: #2f2f2f;
    --ink-soft: #5a5a5a;
    --rule: #bdbdbd;
    --panel-top: #f4f4f4;
    --panel-bottom: #dcdcdc;
    --stripe-cyan: #29aee0;
    --stripe-magenta: #e0287e;
    --stripe-yellow: #f3e31c;
  }
  * { box-sizing: border-box; margin: 0; padding: 0; }
  html, body { width: 1200px; height: 1129px; overflow: hidden; }
  body {
    background: var(--page-bg);
    font-family: "Open Sans", Arial, sans-serif;
    color: var(--ink);
    display: flex;
    align-items: center;
    justify-content: center;
    gap: 80px;
  }
  .card {
    width: 440px;
    height: 760px;
    background: var(--card-white);
    box-shadow: 0 6px 18px rgba(0,0,0,0.18);
    position: relative;
    overflow: hidden;
  }

  /* Front */
  .card-front {
    display: flex;
    flex-direction: column;
    align-items: center;
    justify-content: center;
    gap: 22px;
  }
  .brand-mark {
    width: 84px; height: 84px;
    border-radius: 50%;
    background: var(--brand-orange);
    flex: none;
  }
  .brand-name {
    font-weight: 400;
    color: var(--brand-red);
    font-size: 40px;
    letter-spacing: 1px;
    white-space: nowrap;
  }
  .service-list {
    list-style: none;
    margin-top: 14px;
    text-align: center;
    font-size: 16px;
    line-height: 1.9;
    color: var(--ink-soft);
  }
  .service-list li::before {
    content: "";
    display: inline-block;
    width: 6px; height: 6px;
    border-radius: 50%;
    background: var(--brand-orange);
    margin-right: 10px;
    vertical-align: middle;
  }

  /* Back */
  .card-back { display: flex; flex-direction: column; }
  .back-header {
    height: 130px;
    display: flex;
    align-items: center;
    gap: 18px;
    padding-left: 40px;
  }
  .back-header .brand-mark { width: 58px; height: 58px; }
  .back-header .brand-name { font-size: 30px; }
  .colour-stripe { display: flex; height: 7px; }
  .colour-stripe span { flex: 1; }
  .stripe-cyan { background: var(--stripe-cyan); }
  .stripe-magenta { background: var(--stripe-magenta); }
  .stripe-yellow { background: var(--stripe-yellow); }

  .contact-list {
    flex: 1;
    list-style: none;
    background: linear-gradient(180deg, var(--panel-top), var(--panel-bottom));
    display: flex;
    flex-direction: column;
  }
  .contact-item {
    flex: 1;
    display: flex;
    align-items: center;
    gap: 26px;
    padding: 0 30px 0 34px;
    border-bottom: 1px solid var(--rule);
    font-size: 18px;
    line-height: 1.3;
  }
  .contact-item:last-child { border-bottom: none; }
  .contact-icon {
    flex: none;
    width: 52px; height: 52px;
    border-radius: 50%;
    background: var(--brand-red);
    display: flex; align-items: center; justify-content: center;
  }
  .contact-icon svg { width: 26px; height: 26px; fill: #fff; }
  .person-name { font-size: 25px; font-weight: 700; letter-spacing: 1px; display: block; text-transform: uppercase; }
  .person-role { font-size: 17px; display: block; }
  .detail-label { display: block; font-size: 14px; color: var(--ink-soft); }
  .detail-value { display: block; font-size: 17px; }

  .back-footer { height: 205px; background: var(--brand-red); }
</style>
</head>
<body>
  <section class="card card-front">
    <div class="brand-mark"></div>
    <div class="brand-name">Stretch Bellies</div>
    <ul class="service-list">
      <li>Pre and Post Natal Yoga</li>
      <li>Pregnancy Workshops</li>
      <li>Hypnobirthing Courses</li>
    </ul>
  </section>

  <section class="card card-back">
    <header class="back-header">
      <div class="brand-mark"></div>
      <div class="brand-name">Stretch Bellies</div>
    </header>
    <div class="colour-stripe">
      <span class="stripe-cyan"></span><span class="stripe-magenta"></span><span class="stripe-yellow"></span>
    </div>
    <ul class="contact-list">
      <li class="contact-item">
        <span class="contact-icon"><svg viewBox="0 0 24 24"><circle cx="12" cy="8" r="5"/><path d="M3 22c0-5 4-8 9-8s9 3 9 8z"/></svg></span>
        <span><span class="person-name">Marla Pennick</span><span class="person-role">Marketing Director</span></span>
      </li>
      <li class="contact-item">
        <span class="contact-icon"><svg viewBox="0 0 24 24"><path d="M7 1h10a2 2 0 0 1 2 2v18a2 2 0 0 1-2 2H7a2 2 0 0 1-2-2V3a2 2 0 0 1 2-2zm0 3v14h10V4zm5 15.5a1.2 1.2 0 1 0 0 2.4 1.2 1.2 0 0 0 0-2.4z"/></svg></span>
        <span><span class="detail-label">Mobile</span><span class="detail-value">0491 352 718</span></span>
      </li>
      <li class="contact-item">
        <span class="contact-icon"><svg viewBox="0 0 24 24"><path d="M3 3h18v13H9l-5 5v-5H3z"/></svg></span>
        <span><span class="detail-label">Facebook page</span><span class="detail-value">stretchbelliesbayridgefield</span></span>
      </li>
      <li class="contact-item">
        <span class="contact-icon"><svg viewBox="0 0 24 24"><path d="M12 1a8 8 0 0 0-8 8c0 6 8 14 8 14s8-8 8-14a8 8 0 0 0-8-8zm0 11a3 3 0 1 1 0-6 3 3 0 0 1 0 6z"/></svg></span>
        <span>PO Box 20417 Harlow Street<br>West Brindale 8112 Australia</span>
      </li>
    </ul>
    <footer class="back-footer"></footer>
  </section>
</body>
</html>
```